Business Card Design

Want something very unique. No business, just personal. The image I submitted is for inspiration only.

Target Market(s)

friends and new acquaintances

Industry/Entity Type

Business

Contact Information for Business Card

Dora Malcott
Alder Mesa, NM
505-718-2946
doramalcott@quellmail.net

```html
<!DOCTYPE html>
<html lang="en">
<head>
<meta charset="utf-8">
<title>Dora Malcott – Business Card</title>
<link rel="stylesheet" href="https://fonts.googleapis.com/css2?family=Almendra+SC&family=Marcellus&display=swap">
<style>
  :root {
    --page: #eeeae4;
    --charcoal: #2b2927;
    --ink: #1c1b1a;
    --gold: #f1b013;
    --white: #ffffff;
    --photo-light: #c9b48e;
    --photo-mid: #8f7a55;
    --photo-dark: #5d6b3c;
  }
  * { margin: 0; padding: 0; box-sizing: border-box; }
  html, body {
    width: 1200px; height: 504px; overflow: hidden;
    background: var(--page);
  }
  .sheet {
    position: relative; width: 1200px; height: 504px;
    display: flex; align-items: center; justify-content: center; gap: 30px;
  }
  .card {
    position: relative; width: 560px; height: 320px; overflow: hidden;
    box-shadow: 0 4px 14px rgba(0,0,0,.25);
  }
  .card-front .shapes { position: absolute; inset: 0; }
  .holder-name {
    position: absolute; left: 36px; top: 108px; width: 250px;
    font-family: "Almendra SC", serif; font-weight: 400;
    font-size: 48px; line-height: 52px;
    color: var(--white); text-align: center; letter-spacing: 1px;
  }
  .contact {
    position: absolute; right: 28px; top: 66px; width: 220px;
    font-family: "Marcellus", serif; color: var(--ink); text-align: right;
  }
  .contact-line {
    display: flex; align-items: center; justify-content: flex-end; gap: 5px;
    font-size: 15px; line-height: 30px; white-space: nowrap;
  }
  .contact-line.email { font-size: 13.5px; }
  .contact-line svg { flex: none; width: 13px; height: 13px; fill: var(--ink); }
  .follow { margin-top: 20px; font-size: 15px; line-height: 20px; }
  .networks {
    display: flex; justify-content: flex-end; gap: 8px; margin-top: 4px;
    font-size: 11px; line-height: 14px; white-space: nowrap;
  }
  .network { display: flex; align-items: center; gap: 3px; }
  .network::before {
    content: ""; width: 8px; height: 8px; background: var(--ink);
  }
  .card-back .photo {
    width: 100%; height: 100%;
    background: linear-gradient(135deg, var(--photo-mid) 0%, var(--photo-light) 40%, var(--photo-dark) 100%);
  }
</style>
</head>
<body>
<main class="sheet">
  <section class="card card-front">
    <svg class="shapes" viewBox="0 0 560 320" width="560" height="320" aria-hidden="true">
      <rect width="560" height="320" fill="var(--charcoal)"/>
      <path d="M300 0 C248 80 252 240 380 320 L560 320 L560 0 Z" fill="var(--gold)"/>
      <path d="M306 8 C262 100 276 250 404 320 L392 320 C266 250 252 104 306 8 Z" fill="var(--ink)"/>
      <path d="M318 20 C282 110 296 252 420 320 L414 320 C292 254 276 114 318 20 Z" fill="var(--ink)"/>
    </svg>
    <h1 class="holder-name">Dora<br>Malcott</h1>
    <div class="contact">
      <p class="contact-line">
        <svg viewBox="0 0 24 24"><path d="M12 2a7 7 0 0 0-7 7c0 5 7 13 7 13s7-8 7-13a7 7 0 0 0-7-7zm0 9.5A2.5 2.5 0 1 1 12 6.5a2.5 2.5 0 0 1 0 5z"/></svg>
        <span>Alder Mesa, NM</span>
      </p>
      <p class="contact-line">
        <svg viewBox="0 0 24 24"><path d="M6.6 10.8a15 15 0 0 0 6.6 6.6l2.2-2.2a1 1 0 0 1 1-.25 11.4 11.4 0 0 0 3.6.57 1 1 0 0 1 1 1V20a1 1 0 0 1-1 1A17 17 0 0 1 3 4a1 1 0 0 1 1-1h3.5a1 1 0 0 1 1 1c0 1.25.2 2.450.57 3.57a1 1 0 0 1-.25 1z"/></svg>
        <span>505-718-2946</span>
      </p>
      <p class="contact-line email">
        <svg viewBox="0 0 24 24"><path d="M3 6h18v12H3z M3 6l9 7 9-7" fill="none" stroke="#1c1b1a" stroke-width="2"/></svg>
        <span>doramalcott@quellmail.net</span>
      </p>
      <p class="follow">Follow Us On</p>
      <div class="networks">
        <span class="network">Friendloop</span>
        <span class="network">Peepline</span>
        <span class="network">Workweb</span>
      </div>
    </div>
  </section>
  <section class="card card-back">
    <div class="photo" role="img" aria-label="Photograph of two people crouching beside resting cheetahs in a sunny enclosure with rocks"></div>
  </section>
</main>
</body>
</html>
```